Computer consultant business card

Bexil Software is a newly started computer consulting company. It's a small one-man company that provides mostly Vornix applications but also websites in collaboration with designers. I'm running this company on the side of full time university studies.

I want the final design to be clean and memorable. Be creative! :)

Some inspiration:
http://www.pixelmarta.com/design/48317
http://www.pixelmarta.com/design/2739164/business-card-design-by-frostlynk
http://www.pixelmarta.com/design/604281/business-card-design-by-koralind-vestrabanu

See attachment for my company logo.
Updates

I would like to thank everyone for submitting! I'll need a couple of days to review and ultimately select a design.

Target Market(s)

Non-technical entrepreneurs and small companies.

Industry/Entity Type

University

Requirements
Must have
• My company logo.
In any way, both colors from my logo.
First- and last name, e-mail and phone number.
Double-sided design.
Nice to have
• Something creative with the symbol in my logo

```html
<!DOCTYPE html>
<html lang="en">
<head>
<meta charset="utf-8">
<title>Vexlo – Business Card</title>
<link rel="stylesheet" href="https://fonts.googleapis.com/css2?family=Oswald:wght@500;600&family=Open+Sans:wght@400;600&display=swap">
<style>
  :root {
    --brand-blue: #4a7bc6;
    --ink: #2a2a2a;
    --muted: #6b6b6b;
    --paper: #fbfbfb;
    --strip: #e8e8e8;
    --backdrop: #e4e1dd;
  }
  * { box-sizing: border-box; margin: 0; padding: 0; }
  html, body { width: 1200px; height: 576px; overflow: hidden; }
  body {
    background: var(--backdrop);
    font-family: "Open Sans", Arial, sans-serif;
    position: relative;
  }
  .card {
    position: absolute;
    top: 26px;
    width: 300px;
    height: 524px;
    background: var(--paper);
    box-shadow: 0 4px 14px rgba(0,0,0,.18);
    overflow: hidden;
  }
  .card--back { left: 270px; }
  .card--front { left: 630px; }

  /* wordmark */
  .wordmark { display: flex; align-items: center; gap: 10px; color: var(--ink); font-weight: 600; white-space: nowrap; }
  .wordmark__dot { border-radius: 50%; background: var(--brand-blue); flex: none; }

  /* back side */
  .back__band { position: absolute; top: 0; left: 0; right: 0; height: 12px; background: var(--brand-blue); }
  .back__mark { position: absolute; top: 46px; left: 32px; font-size: 26px; }
  .back__mark .wordmark__dot { width: 22px; height: 22px; }
  .name-tag {
    position: absolute; top: 128px; left: 0;
    width: 220px; height: 44px;
    background: var(--brand-blue);
    clip-path: polygon(0 0, 100% 0, 86% 100%, 0 100%);
    color: #fff;
    font-family: "Oswald", "Arial Narrow", sans-serif;
    font-weight: 600; font-size: 24px; letter-spacing: .5px;
    line-height: 44px; padding-left: 32px; white-space: nowrap;
  }
  .role { position: absolute; top: 180px; left: 32px; font-size: 14px; color: var(--muted); }
  .contacts { position: absolute; top: 270px; left: 0; right: 0; list-style: none; }
  .contact {
    display: flex; align-items: center; gap: 12px;
    height: 42px; margin-bottom: 14px;
    background: var(--strip);
    padding-left: 32px;
    font-size: 13px; color: var(--muted); white-space: nowrap;
  }
  .contact svg { width: 14px; height: 14px; fill: var(--muted); flex: none; }

  /* front side */
  .front__mark { position: absolute; top: 158px; left: 40px; font-size: 60px; letter-spacing: -1px; }
  .front__mark .wordmark__dot { width: 50px; height: 50px; }
  .company-band {
    position: absolute; top: 262px; left: 0;
    width: 250px; height: 54px;
    background: var(--brand-blue);
    color: #fff;
    font-family: "Oswald", "Arial Narrow", sans-serif;
    font-weight: 600; font-size: 27px; letter-spacing: .5px;
    line-height: 54px; padding-left: 40px; white-space: nowrap;
  }
  .company-strip {
    position: absolute; top: 316px; left: 22px;
    width: 250px; height: 110px;
    background: var(--strip);
  }
  .company-site {
    position: absolute; top: 326px; left: 40px;
    font-size: 13px; color: var(--ink);
  }
</style>
</head>
<body>

<section class="card card--back" aria-label="Card back">
  <div class="back__band"></div>
  <div class="wordmark back__mark"><span class="wordmark__dot"></span>vexlo</div>
  <div class="name-tag">MARA VENTLE</div>
  <p class="role">software developer</p>
  <ul class="contacts">
    <li class="contact">
      <svg viewBox="0 0 16 16" aria-hidden="true"><path d="M8 0a8 8 0 100 16A8 8 0 008 0zm0 1.5c.7 0 1.6 1.4 2 3.5H6c.4-2.1 1.3-3.5 2-3.5zM5.8 6.5h4.4a13 13 0 010 3H5.8a13 13 0 010-3zM1.6 6.5h2.7a15 15 0 000 3H1.6a6.5 6.5 0 010-3zm10.1 0h2.7a6.5 6.5 0 010 3h-2.7a15 15 0 000-3zM6 11h4c-.4 2.1-1.3 3.5-2 3.5S6.4 13.1 6 11z"/></svg>
      www.vexlostudio.net
    </li>
    <li class="contact">
      <svg viewBox="0 0 16 16" aria-hidden="true"><path d="M3.6 1l2.3 3-1.3 1.7a9 9 0 005.7 5.7l1.7-1.3 3 2.3-1.5 2.6C7.6 15 1 8.4 1 2.5z"/></svg>
      +(555) 0142 7789
    </li>
    <li class="contact">
      <svg viewBox="0 0 16 16" aria-hidden="true"><path d="M4.5 0h7a1 1 0 011 1v14a1 1 0 01-1 1h-7a1 1 0 01-1-1V1a1 1 0 011-1zm.5 2v10h6V2zm3 11a1 1 0 100 2 1 1 0 000-2z"/></svg>
      +(555) 0186 3304
    </li>
    <li class="contact">
      <svg viewBox="0 0 16 16" aria-hidden="true"><path d="M0 3h16v10H0zm1.5 1.5v.4L8 9l6.5-4.1v-.4zm0 2.2v4.8h13V6.7L8 10.8z"/></svg>
      mara@vexlostudio.net
    </li>
  </ul>
</section>

<section class="card card--front" aria-label="Card front">
  <div class="wordmark front__mark"><span class="wordmark__dot"></span>vexlo</div>
  <div class="company-strip"></div>
  <div class="company-band">COMPANY NAME</div>
  <p class="company-site">www.vexlostudio.net</p>
</section>

</body>
</html>
```